Package Card - Horse Products

I require a card design for the top of a package (see photo). This product is a number holder that gets pinned on to a horse bridle or saddle blanket for competitions. It is a high quality, genuine leather, and premium product.Card is 15cm across and 6cm high. Requirements:Must have - Logo, -"Equestrian Number Holder"- Place on back for barcodeAnything else is up to you! Suggestions and ideas welcome. Card back colour can be any colour.My outcome is for it to look like a premium product

Target Market(s)

High end equestrian competitors

Colors
fbf289

Requirements
Must have
• Logo
• "Equestrian Number Holder"
• "Genuine Leather"
• Room on the back for a barcode sticker
Nice to have
• Should look up market and elegant

```html
<!DOCTYPE html>
<html lang="en">
<head>
<meta charset="UTF-8">
<title>Tide Hollow Equestrian – Number Holder Package Card</title>
<link href="https://fonts.googleapis.com/css2?family=Cinzel:wght@400;600&display=swap" rel="stylesheet">
<style>
  :root {
    --bg: #060708;
    --ink: #ffffff;
    --gold: #e2b256;
    --gold-deep: #c4843a;
    --gold-light: #f8d27a;
  }
  * { margin: 0; padding: 0; box-sizing: border-box; }
  html, body {
    width: 1200px;
    height: 960px;
    overflow: hidden;
    background: var(--bg);
  }
  .card {
    position: relative;
    width: 1200px;
    height: 960px;
    background: var(--bg);
    overflow: hidden;
    font-family: "Cinzel", serif;
  }
  .face {
    position: absolute;
    inset: 0;
  }
  .face--flipped { transform: rotate(180deg); }
  .wave {
    position: absolute;
    left: 0;
    top: 0;
    width: 1200px;
    height: 960px;
  }
  .label {
    position: absolute;
    color: var(--ink);
    font-weight: 400;
    white-space: nowrap;
    line-height: 1;
  }
  .label--material {
    left: 54px;
    top: 826px;
    font-size: 35px;
    letter-spacing: 1px;
  }
  .label--product {
    left: 196px;
    top: 872px;
    font-size: 54px;
    letter-spacing: 1px;
  }
  .brand {
    position: absolute;
    left: 298px;
    top: 598px;
    color: var(--gold);
    font-weight: 600;
    line-height: 1;
    white-space: nowrap;
  }
  .brand__name {
    display: block;
    font-size: 64px;
    letter-spacing: 0.5px;
  }
  .brand__sub {
    display: block;
    margin-top: 6px;
    font-size: 38px;
    letter-spacing: 1px;
  }
</style>
</head>
<body>
<main class="card">
  <section class="face face--upright">
    <svg class="wave" viewBox="0 0 1200 960" aria-hidden="true">
      <defs>
        <linearGradient id="ribbon-a" x1="0" y1="0" x2="1" y2="0">
          <stop offset="0" stop-color="var(--gold-deep)"/>
          <stop offset="0.2" stop-color="var(--gold-light)"/>
          <stop offset="0.55" stop-color="var(--gold-deep)"/>
          <stop offset="1" stop-color="var(--gold)"/>
        </linearGradient>
      </defs>
      <path fill="url(#ribbon-a)" d="M0,724 C300,715 600,790 880,835 C1000,852 1100,800 1200,745 L1200,752 C1100,812 1000,868 860,852 C560,818 300,790 0,800 Z"/>
    </svg>
    <div class="brand">
      <span class="brand__name">TIDE HOLLOW</span>
      <span class="brand__sub">EQUESTRIAN</span>
    </div>
    <p class="label label--material">Genuine Leather</p>
    <p class="label label--product">Equestrian Number Holder</p>
  </section>

  <section class="face face--flipped">
    <svg class="wave" viewBox="0 0 1200 960" aria-hidden="true">
      <defs>
        <linearGradient id="ribbon-b" x1="0" y1="0" x2="1" y2="0">
          <stop offset="0" stop-color="var(--gold-deep)"/>
          <stop offset="0.2" stop-color="var(--gold-light)"/>
          <stop offset="0.55" stop-color="var(--gold-deep)"/>
          <stop offset="1" stop-color="var(--gold)"/>
        </linearGradient>
      </defs>
      <path fill="url(#ribbon-b)" d="M0,724 C300,715 600,790 880,835 C1000,852 1100,800 1200,745 L1200,752 C1100,812 1000,868 860,852 C560,818 300,790 0,800 Z"/>
    </svg>
    <div class="brand">
      <span class="brand__name">TIDE HOLLOW</span>
      <span class="brand__sub">EQUESTRIAN</span>
    </div>
    <p class="label label--material">Genuine Leather</p>
    <p class="label label--product">Equestrian Number Holder</p>
  </section>
</main>
</body>
</html>
```